Create a memorable Web Design for real estate branding

we are a Minnepolis brokerage and boutique housing specialist with over 27 years of experience in the Global furnished housing industry, servicing the Greater Los Angeles area. Specializing in “warm environments” we offer a customized approach to satisfying our guests and client’s needs by offering a wide array of options in highly desirable areas. Additionally, Lantern Dwelling Partners offers assistance and expertise to home buyers, sellers and investors.

Industry/Entity Type

Real Estate

Number of Pages Required

1 page

Font styles to use
Serif
Sans Serif
Decorative

```html
<!DOCTYPE html>
<html lang="en">
<head>
<meta charset="utf-8">
<title>Lantern Dwelling Partners – Real Estate</title>
<link rel="stylesheet" href="https://fonts.googleapis.com/css2?family=Cinzel:wght@400;700&family=Open+Sans:ital,wght@0,400;0,600;1,400&family=Raleway:wght@600;700&display=swap">
<style>
:root{
  --teal:#1a9a86;
  --teal-dark:#137a6a;
  --brand:#5aa83c;
  --ink:#333;
  --muted:#555;
  --soft:#f5f5f5;
  --band:#efefef;
  --footer:#1a1a1a;
  --footer-text:#d8d8d8;
  --white:#fff;
}
*{box-sizing:border-box;margin:0;padding:0}
html,body{width:1200px;height:2222px;overflow:hidden}
body{position:relative;background:var(--white);font-family:"Open Sans",Arial,sans-serif;color:var(--ink)}
.abs{position:absolute}
.serif{font-family:"Cinzel",Georgia,serif}

/* header */
.site-header{position:absolute;left:0;top:0;width:1200px;height:145px;border-top:4px solid var(--teal);background:var(--white)}
.brand{position:absolute;left:99px;top:38px;font-family:"Cinzel",Georgia,serif;font-weight:700;color:var(--brand);font-size:30px;line-height:34px;letter-spacing:1px}
.header-phone{position:absolute;left:963px;top:40px;display:flex;align-items:center;gap:8px;font-family:"Cinzel",Georgia,serif;font-size:18px;color:#222}
.main-nav{position:absolute;top:92px;left:0;width:1200px;font-family:"Cinzel",Georgia,serif;font-size:15px;color:#222}
.main-nav span{position:absolute;white-space:nowrap}
.main-nav .active{color:var(--teal)}

/* hero */
.hero{position:absolute;left:0;top:145px;width:1200px;height:514px;background:linear-gradient(180deg,#8fb7da 0%,#c9dcea 38%,#9fb3a8 62%,#4f7d3d 80%,#3d6a2f 100%)}
.hero-caption{position:absolute;left:207px;top:358px;width:778px;height:89px;background:rgba(40,50,60,.72);color:var(--white);font-family:"Cinzel",Georgia,serif;font-size:31px;letter-spacing:1px;display:flex;align-items:center;justify-content:center}
.hero-arrow{position:absolute;top:383px}

/* welcome */
.video{position:absolute;left:98px;top:718px;width:401px;height:245px;border:4px solid #222;box-shadow:0 10px 14px rgba(0,0,0,.35);background:linear-gradient(180deg,#9cc4e6 0%,#cfe0ea 35%,#7fa06e 60%,#5e8f3e 100%)}
.video-bar{position:absolute;left:0;bottom:0;width:100%;height:30px;background:#1b1b1b}
.welcome-title{position:absolute;left:527px;top:715px;font-family:"Cinzel",Georgia,serif;font-size:30px;color:var(--teal);font-weight:400}
.welcome-text{position:absolute;left:527px;top:757px;width:575px;font-size:12.4px;line-height:22px;color:var(--muted)}
.btn{position:absolute;display:flex;align-items:center;justify-content:center;background:linear-gradient(180deg,#22a690,var(--teal-dark));color:var(--white);font-size:13px;border-radius:3px}

/* services */
.services{position:absolute;left:0;top:1007px;width:1200px;height:400px;background:var(--soft);border-top:1px solid #e6e6e6}
.section-title{font-family:"Cinzel",Georgia,serif;color:var(--teal);font-weight:400}
.services .section-title{position:absolute;top:38px;width:100%;text-align:center;font-size:30px}
.services-sub{position:absolute;top:89px;width:100%;text-align:center;font-style:italic;font-size:13px;color:var(--muted)}
.service{position:absolute;top:148px;width:250px;text-align:center}
.service svg{display:block;margin:0 auto}
.service h3{margin-top:24px;font-family:"Raleway",Arial,sans-serif;font-weight:700;font-size:15.5px;color:#222;letter-spacing:.3px}
.service p{margin-top:12px;font-size:12.5px;line-height:21.5px;color:var(--muted)}

/* news & testimonials */
.news-title,.testi-title{position:absolute;top:1455px;font-size:24px}
.news-item{position:absolute;left:102px;width:520px}
.news-thumb{position:absolute;left:0;top:0;width:150px;height:115px;border:3px solid var(--white);box-shadow:0 0 0 1px #ddd}
.news-body{position:absolute;left:168px;top:0;width:350px}
.news-body h4{font-family:"Raleway",Arial,sans-serif;font-weight:600;font-size:14.5px;color:#222}
.news-date{margin-top:12px;display:flex;align-items:center;gap:8px;font-size:13px;color:var(--teal)}
.news-body p{margin-top:8px;font-size:12.3px;line-height:21px;color:var(--muted)}
.quote-box{position:absolute;left:670px;top:1504px;width:435px;height:151px;background:#f7f7f7;border:1px solid #e5e5e5;border-radius:3px}
.quote-box p{position:absolute;left:38px;top:28px;width:370px;font-style:italic;font-size:12.3px;line-height:23.5px;color:#888}
.avatar{position:absolute;left:685px;top:1677px;width:72px;height:72px;border-radius:50%;border:2px solid #e2e2e2;background:linear-gradient(180deg,#d9cbbd,#8c8f97)}
.testi-name{position:absolute;left:778px;top:1687px;font-style:italic;font-size:15px;color:var(--teal)}
.testi-name span{color:#333}
.mini-arrow{position:absolute;top:1724px;width:20px;height:18px;border:1px solid #ddd;background:var(--white);display:flex;align-items:center;justify-content:center}

/* partners */
.partners{position:absolute;left:5px;top:1837px;width:1195px;height:101px;background:var(--band);border:1px solid #dcdcdc}
.partner{position:absolute;top:36px;height:30px;background:#a7a7a7;border-radius:3px}

/* footer */
.site-footer{position:absolute;left:0;top:1938px;width:1200px;height:284px;background:var(--footer);color:var(--footer-text)}
.footer-brand{position:absolute;left:99px;top:80px;font-family:"Cinzel",Georgia,serif;font-weight:700;font-size:25px;line-height:30px;color:var(--white)}
.footer-col-title{position:absolute;top:28px;font-family:"Cinzel",Georgia,serif;font-size:18px;color:var(--white);letter-spacing:.5px}
.quick-links{position:absolute;left:353px;top:62px;list-style:none;font-size:12.5px;line-height:27.5px;color:var(--white)}
.newsletter-text{position:absolute;left:569px;top:62px;width:250px;font-size:12.5px;line-height:20px;color:var(--white)}
.email-field{position:absolute;left:569px;top:114px;width:262px;height:32px;background:var(--white);color:#444;font-size:12.5px;padding-left:14px;display:flex;align-items:center}
.contact-line{position:absolute;left:910px;display:flex;gap:12px;font-size:12.5px;line-height:18px;color:var(--white)}
.contact-line svg{flex:none;margin-top:2px}
.footer-rule{position:absolute;left:97px;top:217px;width:1006px;height:1px;background:#333}
.copyright{position:absolute;left:97px;top:240px;font-size:12px;color:var(--white)}
.social{position:absolute;top:233px;width:32px;height:32px;border-radius:50%;border:2px solid #444}
</style>
</head>
<body>

<header class="site-header">
  <div class="brand">Lantern Dwelling<br>Partners</div>
  <div class="header-phone">
    <svg width="22" height="22" viewBox="0 0 22 22" aria-hidden="true"><circle cx="11" cy="11" r="9.5" fill="none" stroke="#1a9a86" stroke-width="1.8"/><path d="M7.5 6.5l2 0 1 2.5-1.3 1c.6 1.3 1.5 2.2 2.8 2.8l1-1.3 2.5 1v2c-4.5.3-8.3-3.5-8-8z" fill="#1a9a86"/></svg>
    555-204-0034
  </div>
  <nav class="main-nav">
    <span class="active" style="left:542px">HOME</span>
    <span style="left:631px">ABOUT US</span>
    <span style="left:750px">SERVICES</span>
    <span style="left:862px">NEWS</span>
    <span style="left:948px">CONTACT US</span>
    <svg style="position:absolute;left:1087px;top:3px" width="14" height="14" viewBox="0 0 14 14" aria-hidden="true"><circle cx="6" cy="6" r="4.3" fill="none" stroke="#222" stroke-width="2"/><path d="M9 9l4 4" stroke="#222" stroke-width="2.2"/></svg>
  </nav>
</header>

<section class="hero" role="img" aria-label="Modern residential high-rise towers above a landscaped park with trees, lawns and a pond under a blue sky">
  <svg class="hero-arrow" style="left:28px" width="16" height="34" viewBox="0 0 16 34" aria-hidden="true"><path d="M14 2L2 17l12 15" fill="none" stroke="#fff" stroke-width="2"/></svg>
  <svg class="hero-arrow" style="left:1148px" width="16" height="34" viewBox="0 0 16 34" aria-hidden="true"><path d="M2 2l12 15L2 32" fill="none" stroke="#fff" stroke-width="2"/></svg>
</section>
<div class="hero-caption">SPECIALIZING IN “WARM ENVIRONMENTS”</div>

<section class="welcome">
  <div class="video" role="img" aria-label="Video still of a suburban family home with a curving garden path and green lawn">
    <svg style="position:absolute;left:178px;top:110px" width="40" height="30" viewBox="0 0 40 30" aria-hidden="true"><rect width="40" height="30" rx="4" fill="rgba(0,0,0,.6)"/><path d="M16 8l10 7-10 7z" fill="#fff"/></svg>
    <div class="video-bar">
      <svg width="393" height="30" viewBox="0 0 393 30" aria-hidden="true">
        <path d="M14 9l10 6-10 6z" fill="#fff"/>
        <text x="46" y="19" fill="#ccc" font-size="8" font-family="Open Sans,sans-serif">1:38</text>
        <rect x="72" y="13" width="160" height="4" rx="2" fill="#555"/>
        <rect x="72" y="13" width="100" height="4" rx="2" fill="#3b8fd0"/>
        <circle cx="172" cy="15" r="5" fill="#ddd"/>
        <text x="262" y="19" fill="#ccc" font-size="8" font-family="Open Sans,sans-serif">3:12</text>
        <rect x="296" y="8" width="20" height="14" rx="2" fill="#333"/>
        <rect x="326" y="8" width="20" height="14" rx="2" fill="#333"/>
        <text x="329" y="18" fill="#fff" font-size="7" font-weight="700" font-family="Open Sans,sans-serif">HD</text>
        <path d="M362 9h4M362 9v4M377 21h-4M377 21v-4" stroke="#fff" stroke-width="1.5"/>
      </svg>
    </div>
  </div>
  <h1 class="welcome-title">WELCOME TO LANTERN DWELLING</h1>
  <p class="welcome-text">Lorem Ipsum is simply dummy text of the printing and typesetting industry. Lorem Ipsum has been the industry's standard dummy text ever since the 1500s, when an unknown printer took a galley of type and scrambled it to make a type specimen book. It has survived not only five centuries, but also the leap into electronic typesetting, remaining essentially unchanged. It was popularised in the 1960s with the release of Letraset sheets containing Lorem Ipsum passages, and more recentlyLorem Ipsum is simply dummy text of the printing and typesetting industry. Lorem Ipsum has been the industry's standard dummy text ever since the 1500s, when an unknown printer took</p>
  <div class="btn" style="left:527px;top:924px;width:103px;height:37px">Read More</div>
</section>

<section class="services">
  <h2 class="section-title">OUR SERVICES</h2>
  <p class="services-sub">Nam libero tempore, cum soluta nobis est eligendi optio cumque nihil impedit quo minus id quod maxime</p>

  <div class="service" style="left:94px">
    <svg width="80" height="80" viewBox="0 0 80 80" aria-hidden="true"><path d="M20 38V18L40 4l20 14v20" fill="none" stroke="#1a9a86" stroke-width="5"/><text x="40" y="38" text-anchor="middle" font-size="24" font-weight="700" fill="#1a9a86" font-family="Open Sans,sans-serif">$</text><path d="M6 56c10-6 18-6 26 0h16c4 0 4 6 0 6H34c10 4 22 2 38-10v18c-14 10-30 12-48 4H6z" fill="#1a9a86"/></svg>
    <h3>FINANCIAL PLANNING</h3>
    <p>At vero eos et accusamus et ius<br>to odio dignissigdwsamos ducimus qui<br>blanditiis praesentiu sint</p>
  </div>
  <div class="service" style="left:352px">
    <svg width="80" height="80" viewBox="0 0 80 80" aria-hidden="true"><rect x="22" y="6" width="36" height="68" fill="#1a9a86"/><rect x="14" y="72" width="52" height="5" fill="#1a9a86"/><g fill="#f5f5f5"><rect x="28" y="14" width="8" height="8"/><rect x="44" y="14" width="8" height="8"/><rect x="28" y="28" width="8" height="8"/><rect x="44" y="28" width="8" height="8"/><rect x="28" y="42" width="8" height="8"/><rect x="44" y="42" width="8" height="8"/><rect x="35" y="58" width="10" height="16"/></g></svg>
    <h3>RAEL ESTATE</h3>
    <p>At vero eos et accusamus et ius<br>to odio dignissigdwsamos ducimus qui<br>blanditiis praesentiu sint</p>
  </div>
  <div class="service" style="left:611px">
    <svg width="100" height="80" viewBox="0 0 100 80" aria-hidden="true"><path d="M4 26l14-10 12 20-14 10z M96 26L82 16 70 36l14 10z" fill="#1a9a86"/><path d="M28 26l14-6 10 4 10-4 12 8-8 14-16-10-8 6-8-4 6-6z" fill="#1a9a86"/><path d="M22 42l8-6 24 18c3 3-1 8-5 5l-4-3 2 2c3 3-1 7-4 4l-3-2 1 1c2 3-2 6-4 3l-4-3c2 3-2 5-4 3z" fill="#1a9a86"/></svg>
    <h3>BROKERAGE</h3>
    <p>At vero eos et accusamus et ius<br>to odio dignissigdwsamos ducimus qui<br>blanditiis praesentiu sint</p>
  </div>
  <div class="service" style="left:871px">
    <svg width="80" height="80" viewBox="0 0 80 80" aria-hidden="true"><rect x="12" y="12" width="44" height="60" fill="none" stroke="#1a9a86" stroke-width="4"/><rect x="22" y="6" width="44" height="60" fill="#f5f5f5" stroke="#1a9a86" stroke-width="4"/><path d="M48 14a10 10 0 1 0 10 10H48z" fill="#1a9a86"/><g stroke="#1a9a86" stroke-width="3"><path d="M30 42l2 2 4-4M40 42h18M30 52l2 2 4-4M40 52h18"/></g></svg>
    <h3>ASSESSMENT</h3>
    <p>At vero eos et accusamus et ius<br>to odio dignissigdwsamos ducimus qui<br>blanditiis praesentiu sint</p>
  </div>
</section>

<h2 class="section-title news-title" style="left:102px">OUR NEWS</h2>
<article class="news-item" style="top:1504px">
  <div class="news-thumb" role="img" aria-label="Business person signing a document in front of city skyscrapers" style="background:linear-gradient(180deg,#7aa6d6,#c9d9ea 55%,#e9eef3)"></div>
  <div class="news-body">
    <h4>SED UT PERSPICIATIS UNDE OMNIS</h4>
    <div class="news-date"><svg width="14" height="14" viewBox="0 0 14 14" aria-hidden="true"><rect x="1" y="2" width="12" height="11" fill="none" stroke="#1a9a86" stroke-width="1.5"/><path d="M1 5h12M4 1v3M10 1v3" stroke="#1a9a86" stroke-width="1.5"/></svg>05/03/2016</div>
    <p>Praesent vestibulum molestie lacus. Aenean nmmy hendrerit mauris. Phasellus porta. Fusce suscrius mi. Praesent vestibul um molestie Fusce suscrius mi. Praesent</p>
  </div>
</article>
<article class="news-item" style="top:1652px">
  <div class="news-thumb" role="img" aria-label="City skyline of glass towers beside a river" style="background:linear-gradient(180deg,#6e9fd0,#a9c4dc 45%,#5d7d74 80%,#3c5a4c)"></div>
  <div class="news-body">
    <h4>SED UT PERSPICIATIS UNDE OMNIS</h4>
    <div class="news-date"><svg width="14" height="14" viewBox="0 0 14 14" aria-hidden="true"><rect x="1" y="2" width="12" height="11" fill="none" stroke="#1a9a86" stroke-width="1.5"/><path d="M1 5h12M4 1v3M10 1v3" stroke="#1a9a86" stroke-width="1.5"/></svg>05/03/2016</div>
    <p>Praesent vestibulum molestie lacus. Aenean nmmy hendrerit mauris. Phasellus porta. Fusce suscrius mi. Praesent vestibul um molestie Fusce suscrius mi. Praesent</p>
  </div>
</article>

<h2 class="section-title testi-title" style="left:668px">TESTIMONIALS</h2>
<blockquote class="quote-box">
  <svg style="position:absolute;left:14px;top:14px" width="16" height="12" viewBox="0 0 16 12" aria-hidden="true"><text x="0" y="16" font-size="26" fill="#bbb" font-family="Georgia,serif">“</text></svg>
  <p>Lorem ipsum dolor sit amet, consectetur adipiscing elit, sed do smod tempor incididunt ut labore et dolore magna aliqua. Ut enim ad minim veniam, quis nostrud exercitation Lorem ipsum dolor sit amet, consectetur adipiscing elit, sed do eiusmod tempor</p>
  <svg style="position:absolute;left:374px;top:108px" width="18" height="14" viewBox="0 0 18 14" aria-hidden="true"><text x="0" y="22" font-size="26" fill="#bbb" font-family="Georgia,serif">”</text></svg>
  <svg style="position:absolute;left:40px;top:149px" width="20" height="12" viewBox="0 0 20 12" aria-hidden="true"><path d="M0 0l10 11L20 0" fill="#f7f7f7" stroke="#e5e5e5"/><path d="M1 0h18" stroke="#f7f7f7" stroke-width="2"/></svg>
</blockquote>
<div class="avatar" role="img" aria-label="Portrait of the client giving the testimonial"></div>
<div class="testi-name">Mara Quill <span>- IT Manager</span></div>
<div class="mini-arrow" style="left:788px"><svg width="6" height="9" viewBox="0 0 6 9" aria-hidden="true"><path d="M5 1L1.5 4.5 5 8" fill="none" stroke="#1a9a86" stroke-width="1.5"/></svg></div>
<div class="mini-arrow" style="left:812px"><svg width="6" height="9" viewBox="0 0 6 9" aria-hidden="true"><path d="M1 1l3.5 3.5L1 8" fill="none" stroke="#1a9a86" stroke-width="1.5"/></svg></div>

<section class="partners" aria-label="Partners">
  <div class="partner" style="left:129px;width:80px"></div>
  <div class="partner" style="left:268px;width:118px"></div>
  <div class="partner" style="left:440px;width:96px"></div>
  <div class="partner" style="left:605px;width:108px"></div>
  <div class="partner" style="left:797px;width:82px"></div>
  <div class="partner" style="left:953px;width:116px"></div>
</section>

<footer class="site-footer">
  <div class="footer-brand">Lantern Dwelling<br>Partners</div>

  <h3 class="footer-col-title" style="left:353px">QUICK LINKS</h3>
  <ul class="quick-links">
    <li>Home</li><li>About us</li><li>Services</li><li>News</li><li>Contact Us</li>
  </ul>

  <h3 class="footer-col-title" style="left:569px">NEWSLETTER</h3>
  <p class="newsletter-text">Register Your email address to get information ablout us</p>
  <div class="email-field">Email Address</div>
  <div class="btn" style="left:569px;top:163px;width:100px;height:35px">Subscribe</div>

  <h3 class="footer-col-title" style="left:910px">CONTACT US</h3>
  <div class="contact-line" style="top:64px"><svg width="12" height="14" viewBox="0 0 12 14" aria-hidden="true"><path d="M6 13C2 8 1 6 1 5a5 5 0 0 1 10 0c0 1-1 3-5 8z" fill="#fff"/><circle cx="6" cy="5" r="2" fill="#1a1a1a"/></svg><span>Maple 12 Str. 40210, Northbank<br>Riverton</span></div>
  <div class="contact-line" style="top:114px"><svg width="12" height="14" viewBox="0 0 12 14" aria-hidden="true"><path d="M2 1h3l1 3-2 1.5c.8 2 2 3.2 3.5 4L9 8l3 1v3C6 12.5 1.5 7 2 1z" fill="#fff"/></svg><span>555-204-0034</span></div>
  <div class="contact-line" style="top:146px"><svg width="14" height="14" viewBox="0 0 14 14" aria-hidden="true"><rect x="1" y="4" width="12" height="9" fill="#fff"/><rect x="3" y="1" width="7" height="4" fill="#fff"/><rect x="4" y="7" width="6" height="1.5" fill="#1a1a1a"/></svg><span>555-204-0035</span></div>
  <div class="contact-line" style="top:178px"><svg width="14" height="14" viewBox="0 0 14 14" aria-hidden="true"><rect x="1" y="3" width="12" height="9" fill="#fff"/><path d="M1 3l6 5 6-5" fill="none" stroke="#1a1a1a" stroke-width="1.3"/></svg><span>hello@lanterndwelling.com</span></div>

  <div class="footer-rule"></div>
  <p class="copyright">Copyrights © 2016&nbsp; Lantern Dwelling Partners. All rights reserved. Terms and Conditions &nbsp;|&nbsp; Privacy Policy</p>
  <div class="social" style="left:954px;background:#3b5998"></div>
  <div class="social" style="left:991px;background:#2fa8e0"></div>
  <div class="social" style="left:1028px;background:#1e73a8"></div>
  <div class="social" style="left:1065px;background:#f0901e"></div>
</footer>

</body>
</html>
```